jQuery Mobile CSS for web app

Task Outline:
Create jQuery Mobile themeroller compliant CSS and icons for a mobile web app.
Task Description:
Brindle Solutions are in the process of implementing a new, web based version of their Tessel operations platform.
The web based version of Tessel is built on top of the jQuery Mobile platform and we are looking for a designer to create a jQuery Mobile themeroller compliant CSS theme pack that we can plug into our application. The aim is to remove the standard jQuery Mobile look and feel and to introduce the Brindle branding throughout the new web app.
A number of screenshots are shown in the attached design spec (brindle_solutions.pdf) that show what the current (Windows Mobile 6.5) application looks like, alongside the development version of our new web app.
Deliverables:
• jQuery Mobile (v 1.4.2) themeroller compliant CSS which provides theming for all jQuery Mobile UI components.
• Example html showing how to use the CSS theme (especially where additional html/css classes are required).
• New set of status icons (as listed in attachment)
Inspiration:
See our website for current branding: www.brindle-solutions-demo.net

```html
<!DOCTYPE html>
<html lang="en">
<head>
<meta charset="utf-8">
<title>Brindle Tessel – Job Header</title>
<link rel="stylesheet" href="https://fonts.googleapis.com/css2?family=Open+Sans:wght@400&family=Roboto:wght@400&display=swap">
<style>
  :root {
    --brand-red: #d0141e;
    --header-black: #000000;
    --menu-grey: #8a8a8a;
    --menu-border: #6f6f6f;
    --band-grey: #e8e8e8;
    --page-grey: #f4f4f4;
    --field-white: #ffffff;
    --field-border: #e2e2e2;
    --label-grey: #555555;
    --value-dark: #333333;
    --footer-bg: #f7f7f7;
    --footer-border: #dddddd;
    --footer-text: #666666;
    --icon-slate: #5a6b82;
  }
  * { box-sizing: border-box; margin: 0; padding: 0; }
  html, body { width: 819px; height: 1200px; overflow: hidden; }
  body {
    position: relative;
    background: var(--page-grey);
    font-family: "Open Sans", Arial, sans-serif;
  }
  .app-header {
    position: absolute; left: 0; top: 0; width: 819px; height: 163px;
    background: var(--header-black);
  }
  .app-title {
    position: absolute; left: 208px; top: 54px;
    font-family: "Roboto", Arial, sans-serif;
    font-size: 42px; line-height: 1; color: #fff;
  }
  .menu-button {
    position: absolute; left: 686px; top: 48px; width: 74px; height: 70px;
    background: var(--menu-grey); border: 1px solid var(--menu-border);
    border-radius: 6px;
    display: flex; align-items: center; justify-content: center;
  }
  .page-heading {
    position: absolute; left: 0; top: 163px; width: 819px; height: 139px;
    background: var(--band-grey);
  }
  .page-heading h1 {
    position: absolute; left: 43px; top: 47px;
    font-size: 43px; font-weight: 400; line-height: 1.1;
    color: var(--brand-red);
  }
  .field-label {
    position: absolute; left: 44px;
    font-size: 32px; line-height: 1; color: var(--label-grey);
  }
  .field-label .required { color: var(--brand-red); }
  .field-input {
    position: absolute; left: 46px; width: 727px; height: 98px;
    background: var(--field-white); border: 1px solid var(--field-border);
    padding-left: 33px;
    display: flex; align-items: center;
    font-size: 24px; color: var(--value-dark);
  }
  .field-select .caret {
    position: absolute; right: 33px; top: 47px;
  }
  .footer-bar {
    position: absolute; left: 0; top: 1021px; width: 819px; height: 179px;
    display: flex; background: var(--footer-bg);
    border-top: 1px solid var(--footer-border);
  }
  .footer-button {
    flex: 1; position: relative;
    border-right: 2px solid var(--footer-border);
    display: flex; flex-direction: column; align-items: center;
  }
  .footer-button:last-child { border-right: none; }
  .footer-button svg { margin-top: 30px; }
  .footer-button span {
    margin-top: 14px;
    font-size: 34px; line-height: 1; color: var(--footer-text);
  }
  .screen-code {
    position: absolute; left: 770px; top: 1152px;
    font-family: Arial, sans-serif; font-size: 20px; color: #111;
  }
</style>
</head>
<body>
  <header class="app-header">
    <div class="app-title">Brindle Tessel</div>
    <div class="menu-button" aria-label="Menu">
      <svg width="28" height="22" viewBox="0 0 28 22">
        <rect x="1" y="3" width="26" height="3" fill="#333"/>
        <rect x="1" y="10" width="26" height="3" fill="#333"/>
        <rect x="1" y="17" width="26" height="3" fill="#333"/>
      </svg>
    </div>
  </header>

  <section class="page-heading"><h1>Job Header D..</h1></section>

  <div class="field-label" style="top:360px">Customer Name : <span class="required">*</span></div>
  <div class="field-input field-select" style="top:428px">One
    <svg class="caret" width="24" height="18" viewBox="0 0 24 18"><path d="M0 0H24L12 18Z" fill="#999"/></svg>
  </div>

  <div class="field-label" style="top:568px">Customer Reference# : <span class="required">*</span></div>
  <div class="field-input" style="top:636px">Two</div>

  <div class="field-label" style="top:776px">Job Description <span class="required">*</span></div>
  <div class="field-input" style="top:844px">Three</div>

  <nav class="footer-bar">
    <div class="footer-button">
      <svg width="60" height="60" viewBox="0 0 60 60">
        <circle cx="30" cy="30" r="27" fill="none" stroke="var(--brand-red)" stroke-width="4"/>
        <path d="M16 30L28 20V26H43V34H28V40Z" fill="var(--brand-red)"/>
      </svg>
      <span>BACK</span>
    </div>
    <div class="footer-button">
      <svg width="60" height="60" viewBox="0 0 60 60">
        <rect x="9" y="13" width="7" height="6" fill="var(--icon-slate)"/>
        <rect x="20" y="13" width="32" height="6" fill="var(--icon-slate)"/>
        <rect x="9" y="26" width="7" height="6" fill="var(--icon-slate)"/>
        <rect x="20" y="26" width="32" height="6" fill="var(--icon-slate)"/>
        <rect x="9" y="39" width="7" height="6" fill="var(--icon-slate)"/>
        <rect x="20" y="39" width="32" height="6" fill="var(--icon-slate)"/>
      </svg>
      <span>TASKS</span>
    </div>
    <div class="footer-button">
      <svg width="60" height="60" viewBox="0 0 60 60">
        <circle cx="30" cy="30" r="27" fill="none" stroke="var(--brand-red)" stroke-width="4"/>
        <path d="M44 30L32 20V26H17V34H32V40Z" fill="var(--brand-red)"/>
      </svg>
      <span>NEXT</span>
    </div>
  </nav>
  <div class="screen-code">C7</div>
</body>
</html>
```